Banner Ad Design Project

I require banner ad designs with the below wording.

1. Join Today and Make Money Tomorrow. Unlimited Income. Click Here Now

2. I lost my job. Now I Make Over $5,000 Per Week From Home. You Can Too. Free Info, Apply Now

I require sizes: 300x250 and 728x90 and 468x60 and 120x240

The design should communicate legitimate, accredited, online business.

Industry/Entity Type

Business

Requirements
Should not have
• Creative attributes to avoid*
Phone numbers in creative
Creative with no click buttons
Interactive creative
Brand messaging with no call to action
Creative with long looping times

```html
<!DOCTYPE html>
<html lang="en">
<head>
<meta charset="utf-8">
<title>Join Today Banner Set</title>
<link rel="stylesheet" href="https://fonts.googleapis.com/css2?family=Roboto+Condensed:wght@700;800&display=swap">
<style>
  :root {
    --stage-light: #c9c9c9;
    --stage-dark: #8f8f8f;
    --pink: #d81b60;
    --pink-deep: #a80f45;
    --ink: #111111;
    --white: #ffffff;
    --gold-top: #fff7a8;
    --gold-mid: #ffd21f;
    --gold-low: #e79a00;
    --photo-light: #e9e6e3;
    --photo-warm: #b9a69a;
    --cash-light: #cfd8c4;
    --cash-dark: #7f9474;
  }
  * { box-sizing: border-box; margin: 0; padding: 0; }
  html, body { width: 1200px; height: 900px; overflow: hidden; }
  body {
    position: relative;
    background: radial-gradient(ellipse at 50% 40%, var(--stage-light), var(--stage-dark));
    font-family: "Roboto Condensed", "Arial Narrow", sans-serif;
    font-weight: 700;
  }
  .banner { position: absolute; overflow: hidden; }
  .banner > svg.backdrop { position: absolute; inset: 0; width: 100%; height: 100%; }
  .photo, .cash { position: absolute; }
  .photo { background: linear-gradient(160deg, var(--photo-light), var(--photo-warm)); }
  .cash {
    background: linear-gradient(135deg, var(--cash-light), var(--cash-dark));
    transform: rotate(-8deg); border-radius: 4px;
  }
  .line {
    position: absolute; white-space: nowrap; line-height: 1;
    transform: translate(-50%, -50%); color: var(--white);
    text-shadow: 0 1px 2px rgba(0,0,0,.35);
  }
  .gold {
    font-weight: 800;
    background: linear-gradient(180deg, var(--gold-top) 0%, var(--gold-mid) 50%, var(--gold-low) 100%);
    -webkit-background-clip: text; background-clip: text; color: transparent;
    text-shadow: none; filter: drop-shadow(0 2px 1px rgba(0,0,0,.45));
  }
  .cta {
    position: absolute; display: flex; align-items: center; justify-content: center;
    background: linear-gradient(180deg, var(--white), #dcdcdc);
    border-radius: 999px 0 0 999px; font-size: 25px;
    box-shadow: 0 2px 4px rgba(0,0,0,.35);
  }
  .cta--dark { color: var(--ink); }
  .cta--pink { color: var(--pink); }

  .rect-a { left: 108px; top: 96px; width: 450px; height: 374px; }
  .rect-b { left: 591px; top: 96px; width: 450px; height: 374px; }
  .leader-a { left: 62px; top: 527px; width: 1092px; height: 134px; }
  .leader-b { left: 62px; top: 680px; width: 1092px; height: 135px; }
</style>
</head>
<body>

<section class="banner rect-a">
  <svg class="backdrop" viewBox="0 0 450 374" preserveAspectRatio="none">
    <defs>
      <linearGradient id="darkA" x1="0" y1="0" x2="0" y2="1"><stop offset="0" stop-color="#3a3a3a"/><stop offset="1" stop-color="#0d0d0d"/></linearGradient>
      <linearGradient id="pinkA" x1="0" y1="0" x2="0" y2="1"><stop offset="0" stop-color="#e02a6c"/><stop offset="1" stop-color="#a80f45"/></linearGradient>
    </defs>
    <rect width="450" height="374" fill="url(#darkA)"/>
    <path d="M0 300 Q230 250 450 222 L450 374 L0 374 Z" fill="#ffffff"/>
    <path d="M0 310 Q230 262 450 234 L450 374 L0 374 Z" fill="url(#pinkA)"/>
  </svg>
  <div class="photo" style="left:0;top:0;width:140px;height:374px" role="img" aria-label="Photo of a smiling businesswoman in glasses"></div>
  <div class="cash" style="left:190px;top:214px;width:175px;height:108px" role="img" aria-label="Fan of dollar bills"></div>
  <span class="line gold" style="left:290px;top:43px;font-size:57px">Join Today</span>
  <span class="line" style="left:290px;top:93px;font-size:35px">&amp; Make Money Over</span>
  <span class="line gold" style="left:290px;top:138px;font-size:40px">$5,000 Per Week</span>
  <span class="line" style="left:290px;top:184px;font-size:33px">From Home</span>
  <a class="cta cta--dark" style="left:259px;top:312px;width:191px;height:42px">Click Here Now</a>
</section>

<section class="banner rect-b">
  <svg class="backdrop" viewBox="0 0 450 374" preserveAspectRatio="none">
    <defs>
      <linearGradient id="pinkB" x1="0" y1="0" x2="0" y2="1"><stop offset="0" stop-color="#e02a6c"/><stop offset="1" stop-color="#a80f45"/></linearGradient>
    </defs>
    <rect width="450" height="374" fill="url(#pinkB)"/>
    <path d="M70 0 Q100 125 450 150 L450 0 Z" fill="#ffffff"/>
  </svg>
  <div class="photo" style="left:82px;top:0;width:368px;height:142px;clip-path:path('M0 0 Q30 117 368 142 L368 0 Z')" role="img" aria-label="Photo of a cheering businesswoman with raised arms"></div>
  <span class="line gold" style="left:182px;top:180px;font-size:58px">Join Today</span>
  <span class="line" style="left:182px;top:229px;font-size:35px">&amp; Make Money Over</span>
  <span class="line gold" style="left:182px;top:274px;font-size:45px">$5,000 Per Week</span>
  <span class="line" style="left:180px;top:324px;font-size:33px">From Home</span>
  <a class="cta cta--pink" style="left:274px;top:307px;width:176px;height:42px">Apply Now</a>
</section>

<section class="banner leader-a">
  <svg class="backdrop" viewBox="0 0 1092 134" preserveAspectRatio="none">
    <defs>
      <linearGradient id="pinkC" x1="0" y1="0" x2="0" y2="1"><stop offset="0" stop-color="#e02a6c"/><stop offset="1" stop-color="#a80f45"/></linearGradient>
    </defs>
    <rect width="1092" height="134" fill="url(#pinkC)"/>
    <path d="M0 0 L200 0 Q250 67 210 134 L0 134 Z" fill="#ffffff"/>
  </svg>
  <div class="photo" style="left:0;top:0;width:215px;height:134px;clip-path:path('M0 0 L190 0 Q238 67 198 134 L0 134 Z')" role="img" aria-label="Photo of a cheering businesswoman with raised arms"></div>
  <div class="cash" style="left:527px;top:16px;width:165px;height:104px" role="img" aria-label="Fan of dollar bills"></div>
  <span class="line gold" style="left:386px;top:44px;font-size:58px">Join Today</span>
  <span class="line" style="left:386px;top:98px;font-size:35px">&amp; Make Money Over</span>
  <span class="line gold" style="left:881px;top:44px;font-size:52px">$5,000 Per Week</span>
  <span class="line" style="left:805px;top:100px;font-size:36px">From Home</span>
  <a class="cta cta--pink" style="left:916px;top:77px;width:176px;height:43px">Apply Now</a>
</section>

<section class="banner leader-b">
  <svg class="backdrop" viewBox="0 0 1092 135" preserveAspectRatio="none">
    <defs>
      <linearGradient id="darkD" x1="0" y1="0" x2="0" y2="1"><stop offset="0" stop-color="#3a3a3a"/><stop offset="1" stop-color="#0d0d0d"/></linearGradient>
      <linearGradient id="pinkD" x1="0" y1="0" x2="0" y2="1"><stop offset="0" stop-color="#e02a6c"/><stop offset="1" stop-color="#a80f45"/></linearGradient>
    </defs>
    <rect width="1092" height="135" fill="url(#darkD)"/>
    <path d="M580 0 Q500 70 580 135 L1092 135 L1092 0 Z" fill="#ffffff"/>
    <path d="M592 0 Q512 70 592 135 L1092 135 L1092 0 Z" fill="url(#pinkD)"/>
  </svg>
  <div class="photo" style="left:0;top:0;width:89px;height:135px" role="img" aria-label="Photo of a smiling businesswoman in glasses"></div>
  <div class="cash" style="left:445px;top:16px;width:200px;height:104px" role="img" aria-label="Fan of dollar bills"></div>
  <span class="line gold" style="left:265px;top:48px;font-size:58px">Join Today</span>
  <span class="line" style="left:265px;top:100px;font-size:37px">&amp; Make Money Over</span>
  <span class="line gold" style="left:881px;top:45px;font-size:52px">$5,000 Per Week</span>
  <span class="line" style="left:790px;top:102px;font-size:40px">From Home</span>
  <a class="cta cta--dark" style="left:915px;top:82px;width:177px;height:41px">Click Here Now</a>
</section>

</body>
</html>
```